Business Card

Just need business logo with phone number on it. 0487 312 654
And the following on the bottom of the card.

"Your local plumbing experts".
and emblems for zelpa card, cheque and cash

```html
<!DOCTYPE html>
<html lang="en">
<head>
<meta charset="utf-8">
<title>Harbour Line Plumbing – Business Card</title>
<link href="https://fonts.googleapis.com/css2?family=Roboto:ital,wght@0,400;0,500;0,700;1,400&display=swap" rel="stylesheet">
<style>
  :root {
    --backdrop: #e5e5e5;
    --card-white: #f9f9f9;
    --card-panel: #f5f5f3;
    --brand-red: #d9261c;
    --brand-blue: #0a7cc4;
    --text-dark: #444444;
    --text-light: #ffffff;
  }
  * { margin: 0; padding: 0; box-sizing: border-box; }
  html, body {
    width: 1200px; height: 608px; overflow: hidden;
    background: var(--backdrop);
    font-family: "Roboto", Arial, sans-serif;
  }
  .stage { position: relative; width: 1200px; height: 608px; }
  .card {
    position: absolute; top: 206px; width: 327px; height: 197px;
    overflow: hidden;
  }
  .card-front { left: 237px; background: var(--card-white); }
  .card-back { left: 636px; background: var(--card-panel); }

  .brand-name {
    display: flex; align-items: center; gap: 6px;
    color: var(--brand-red); font-weight: 700; text-transform: uppercase;
    letter-spacing: 0.3px; line-height: 1; white-space: nowrap;
  }
  .brand-mark { width: 10px; height: 10px; background: var(--brand-red); flex: none; }

  .card-front .brand-name {
    position: absolute; left: 0; right: 0; top: 86px;
    justify-content: center; font-size: 19px;
  }

  .payments {
    position: absolute; left: 0; right: 0; top: 160px;
    display: flex; justify-content: center; gap: 18px;
    list-style: none;
  }
  .payments li {
    display: flex; align-items: center; gap: 4px;
    color: var(--text-dark); font-size: 8.5px; font-weight: 500; line-height: 1;
  }
  .payments .pay-mark { width: 7px; height: 7px; background: var(--brand-blue); flex: none; }
  .payments svg { width: 12px; height: 8px; flex: none; }

  .card-back .info { position: absolute; left: 0; top: 0; width: 160px; height: 197px; }
  .card-back .brand-name {
    position: absolute; left: 13px; top: 36px; font-size: 9.5px; gap: 4px;
  }
  .card-back .brand-mark { width: 7px; height: 7px; }
  .person { position: absolute; left: 13px; top: 80px; }
  .person-name { color: var(--brand-blue); font-weight: 700; font-size: 14px; }
  .person-role { color: var(--text-dark); font-style: italic; font-size: 8.5px; margin-top: 3px; }

  .contacts { position: absolute; left: 13px; top: 124px; list-style: none; }
  .contacts li {
    display: flex; align-items: center; gap: 4px;
    color: var(--brand-blue); font-size: 8.5px; line-height: 11.5px;
  }
  .contacts li.phone { font-weight: 700; font-size: 10.5px; line-height: 13px; margin-bottom: 1px; }
  .contacts svg { width: 7px; height: 7px; flex: none; }

  .tagline {
    position: absolute; left: 0; top: 176px; width: 168px; height: 21px;
    background: var(--brand-blue);
    clip-path: polygon(0 0, 150px 0, 168px 100%, 0 100%);
    color: var(--text-light); font-size: 9px; line-height: 21px; padding-left: 13px;
  }
  .color-panel { position: absolute; left: 160px; top: 0; width: 167px; height: 197px; }
</style>
</head>
<body>
<div class="stage">
  <section class="card card-front">
    <div class="brand-name"><span class="brand-mark"></span>Harbour Line Plumbing</div>
    <ul class="payments">
      <li><span class="pay-mark"></span>Zelpa</li>
      <li>
        <svg viewBox="0 0 12 8"><rect x="0.5" y="0.5" width="11" height="7" fill="none" stroke="#0a7cc4"/><path d="M2 3h6M2 5.5h4" stroke="#0a7cc4" stroke-width="0.8"/></svg>
        Cheque
      </li>
      <li>
        <svg viewBox="0 0 12 8"><rect x="0.5" y="0.5" width="11" height="7" fill="#0a7cc4"/><circle cx="6" cy="4" r="1.8" fill="#f9f9f9"/></svg>
        Cash
      </li>
    </ul>
  </section>

  <section class="card card-back">
    <div class="info">
      <div class="brand-name"><span class="brand-mark"></span>Harbour Line Plumbing</div>
      <div class="person">
        <div class="person-name">Sam Carter</div>
        <div class="person-role">Plumber</div>
      </div>
      <ul class="contacts">
        <li class="phone">
          <svg viewBox="0 0 10 10"><path fill="#d9261c" d="M1 3c0-1 1-2 4-2s4 1 4 2v1H7V3H3v1H1zM2 5h6l1 4H1z"/></svg>
          0487 312 654
        </li>
        <li>
          <svg viewBox="0 0 10 10"><rect x="0.5" y="2" width="9" height="6" fill="#d9261c"/><path d="M0.5 2l4.5 3.5L9.5 2" stroke="#fff" stroke-width="0.8" fill="none"/></svg>
          sam@harbourline.com
        </li>
        <li>
          <svg viewBox="0 0 10 10"><circle cx="5" cy="5" r="4.2" fill="none" stroke="#d9261c" stroke-width="1.2"/><path d="M1 5h8M5 1v8" stroke="#d9261c" stroke-width="0.9"/></svg>
          www.harbourline.com
        </li>
      </ul>
      <div class="tagline">Your Local Plumbing Experts</div>
    </div>
    <svg class="color-panel" viewBox="0 0 167 197" aria-hidden="true">
      <rect width="167" height="197" fill="#d9261c"/>
      <polygon points="84,0 167,0 167,189 150,189" fill="#0a7cc4"/>
    </svg>
  </section>
</div>
</body>
</html>
```